Web Design Project

We are an IT System Integrator. We provide Korvin 450 ERP System, CRM etc. We also provide hardware, networking servicing. Please look at www.zolvantix.com.sg. They provide the same service as us. We like to redesign our web site. I will attached the color that I prefer for reference.

Our website is www.tadurk.com.sg.  It has been created about 14 years ago.  We are trying to revamp it with a new look and information.   The new website must be informative, fast.    I have attached an attachment which show the color that I prefer(brownish golden).   

Our competitor (www.zolvantix.com) is carrying the same trade as us.  They have all the informations In their website that we will like to have.  Therefore I recommend you to take a look at my competitor website and have a better   
understanding on the kind of information I would like to have for my new website.

This project is guarantee to the person with the best design.  We can have it guarantee.

Target Market(s)

Corporate and companies

Industry/Entity Type

Hardware

```html
<!DOCTYPE html>
<html lang="en">
<head>
<meta charset="utf-8">
<title>Tadurk Information Systems PTE LTD</title>
<link rel="stylesheet" href="https://fonts.googleapis.com/css2?family=Exo+2:wght@400;500&family=Arimo:wght@400;700&display=swap">
<style>
:root{
  --bar:#333333;
  --ink:#2b2b2b;
  --muted:#9a9a9a;
  --gold:#f3b21f;
  --gold-deep:#c98f17;
  --line:#dddddd;
  --white:#ffffff;
}
*{margin:0;padding:0;box-sizing:border-box}
html,body{width:1050px;height:1200px;overflow:hidden;background:var(--white)}
body{position:relative;font-family:"Arimo",Arial,sans-serif;color:var(--ink)}
h1,h2{font-weight:400}
.abs{position:absolute}

.top-bar{left:0;top:0;width:1050px;height:41px;background:var(--bar)}
.top-links{left:653px;top:15px;font-size:10px;color:#eee;letter-spacing:.2px}
.top-links span{margin:0 4px;color:#aaa}
.top-social{left:822px;top:10px;display:flex;gap:10px;align-items:center}
.top-social .net{font-family:"Exo 2",sans-serif;font-size:13px;font-weight:500;color:var(--gold)}

.hero{left:0;top:41px;width:1050px;height:520px;background:linear-gradient(180deg,#d7dde2 0%,#c2c9ce 45%,#9ea7ae 100%)}
.hero-curve{left:0;top:500px}

.brand{left:157px;top:96px;display:flex;align-items:center;gap:8px}
.brand-dot{width:26px;height:26px;border-radius:50%;background:var(--gold-deep);flex:none}
.brand-name{font-family:"Exo 2",sans-serif;font-weight:500;color:var(--ink);font-size:21px;line-height:22px;white-space:nowrap}
.brand-name small{display:block;font-size:14px;line-height:16px;padding-left:44px}

.nav{left:409px;top:41px;display:flex;height:85px}
.nav a{font-family:"Exo 2",sans-serif;font-size:14.5px;color:#1e1e1e;text-decoration:none;text-transform:uppercase;padding-top:40px}
.nav .current{width:51px;background:#222;color:var(--white);text-align:center;border-top:5px solid var(--gold);padding-top:35px;margin-right:12px}
.nav .item{margin-right:19px}

.headline{left:0;width:1050px;top:340px;text-align:center;font-family:"Exo 2",sans-serif;font-size:50px;letter-spacing:-1.5px;color:#2c2c2c}
.subline{left:0;width:1050px;top:396px;text-align:center;font-family:"Exo 2",sans-serif;font-size:15.5px;color:#111}
.dots{left:469px;top:424px;display:flex;gap:14px}
.dots i{width:12px;height:12px;border-radius:50%;background:#e8c97a;display:block}
.dots i.on{background:#b8861a;box-shadow:0 0 0 2px #f4e2b0}
.arrow{top:468px;width:48px;height:48px;border-radius:50%;background:var(--white)}
.arrow svg{position:absolute;left:14px;top:14px}

.service{top:454px;width:120px;height:138px}
.service svg.hex{position:absolute;left:0;top:0}
.service .icon{position:absolute;left:0;width:120px;top:30px;text-align:center}
.service .label{position:absolute;left:0;width:120px;top:86px;text-align:center;font-family:"Exo 2",sans-serif;font-size:14px;color:var(--gold);text-transform:uppercase;line-height:17px}

.about-title{left:163px;top:624px;font-family:"Exo 2",sans-serif;font-size:21.5px;color:#222;text-transform:uppercase}
.about-title em{font-style:normal;color:var(--gold)}
.about-text{left:163px;top:661px;width:492px;font-size:11.3px;line-height:14.6px;color:var(--muted)}
.video{left:661px;top:624px;width:232px;height:103px;border:3px solid #8c8c8c;background:linear-gradient(135deg,#3a3d40 0%,#5b5f63 40%,#c9a45a 55%,#4f7fb8 70%,#2e3033 100%)}
.video .play{position:absolute;left:94px;top:30px;width:38px;height:38px;border-radius:50%;background:rgba(255,255,255,.35)}
.video .play svg{position:absolute;left:13px;top:10px}

.col-title{top:782px;font-family:"Exo 2",sans-serif;font-size:20px;color:#222;text-transform:uppercase}
.map{left:167px;top:812px;width:221px;height:76px;background:linear-gradient(135deg,#e9eee2 0%,#dde6d6 50%,#f2e4b8 100%);border:1px solid #d5d5d5}
.address{left:167px;top:897px;font-size:10px;line-height:18px;color:#555}
.address b{color:#333}
.contact-row{display:flex}
.contact-row b{width:74px}

.event-date{width:34px;height:30px;background:#3a3a3a;color:var(--white);text-align:center;font-family:"Exo 2",sans-serif;line-height:1}
.event-date .d{font-size:17px;display:block;padding-top:1px}
.event-date .m{font-size:8px;font-weight:500;display:block}
.event-text{font-size:9.6px;line-height:11.5px;color:#444}
.partner-name{display:flex;align-items:center;gap:6px;font-family:"Exo 2",sans-serif;font-weight:500;font-size:19px;color:#1d2b6b}
.partner-name i{width:14px;height:14px;background:#5d5fb3;display:block}
.divider-h{height:1px;background:var(--line)}

.quote-mark{font-family:"Exo 2",sans-serif;font-size:30px;color:#555;line-height:1}
.quote-text{font-size:9.2px;line-height:13px;color:#555;width:178px}
.quote-by{width:130px;text-align:right;font-size:9.4px;line-height:12px;color:#666;font-style:italic}
.quote-by b{color:#333}

.partners{left:157px;top:1030px;width:742px;height:54px;border:1px solid #e4e4e4;background:linear-gradient(180deg,#f1f1f1,#fff)}
.partners .label{position:absolute;left:24px;top:15px;font-family:"Exo 2",sans-serif;font-size:19px;color:#222;text-transform:uppercase;letter-spacing:.5px}
.partners .sep{position:absolute;top:8px;width:1px;height:38px;background:#ddd}
.partners .badge{position:absolute;left:313px;top:6px;width:42px;height:42px;border-radius:50%;border:2px solid #2b3f8f;background:#f6f6f6}
.partners .p{position:absolute;top:13px;font-family:"Exo 2",sans-serif;font-weight:500;font-size:20px;white-space:nowrap}

.footer{left:0;top:1094px;width:1050px;height:106px;background:var(--bar)}
.footer-links{left:157px;top:1130px;font-size:10.5px;color:#eee}
.footer-links span{color:var(--gold);margin:0 6px}
.copyright{left:158px;top:1157px;font-size:9.5px;color:#ccc}
.footer-social{left:611px;top:1145px;display:flex;gap:10px}
.footer-social span{width:27px;height:27px;border-radius:50%;background:var(--white);color:#333;font-family:"Exo 2",sans-serif;font-size:9px;font-weight:500;display:flex;align-items:center;justify-content:center}
.footer-brand{left:770px;top:1140px;display:flex;align-items:center;gap:7px}
.footer-brand .brand-dot{width:24px;height:24px}
.footer-brand .brand-name{color:var(--white);font-size:19px;line-height:20px}
.footer-brand .brand-name small{font-size:12px;line-height:14px;padding-left:40px;color:var(--gold)}
</style>
</head>
<body>

<div class="abs top-bar"></div>
<div class="abs top-links">FAQs<span>|</span>Resources<span>|</span>Contact Us</div>
<div class="abs top-social">
  <svg width="22" height="15" viewBox="0 0 22 15" aria-label="Email"><rect x="0" y="0" width="22" height="15" rx="1" fill="#f3b21f"/><path d="M1 1 L11 9 L21 1" fill="none" stroke="#333" stroke-width="1.6"/></svg>
  <span class="net">Qil</span>
  <span class="net">Vox</span>
</div>

<div class="abs hero" role="img" aria-label="Photo of a smiling business team seated together in a bright office"></div>
<svg class="abs hero-curve" width="1050" height="70" viewBox="0 0 1050 70"><path d="M0 58 Q525 -16 1050 58 L1050 70 L0 70 Z" fill="#ffffff"/></svg>

<div class="abs brand">
  <div class="brand-dot"></div>
  <div class="brand-name">Tadurk Information<small>Systems PTE LTD</small></div>
</div>

<nav class="abs nav">
  <a class="current" href="#">Home</a>
  <a class="item" href="#">About Us</a>
  <a class="item" href="#">Solutions</a>
  <a class="item" href="#">Services</a>
  <a class="item" href="#">Event &amp; Promotion</a>
  <a href="#">Our Clients</a>
</nav>

<div class="abs headline">CUSTOMER RELATIONSHIP</div>
<div class="abs subline">Shorten sales cycle and achieve total customer satisfaction.</div>
<div class="abs dots"><i class="on"></i><i></i><i></i><i></i><i></i><i></i></div>

<div class="abs arrow" style="left:36px"><svg width="20" height="20" viewBox="0 0 20 20"><path d="M14 2 L5 10 L14 18" fill="none" stroke="#111" stroke-width="4"/></svg></div>
<div class="abs arrow" style="left:980px"><svg width="20" height="20" viewBox="0 0 20 20"><path d="M6 2 L15 10 L6 18" fill="none" stroke="#111" stroke-width="4"/></svg></div>

<svg width="0" height="0" style="position:absolute">
  <defs><linearGradient id="hexFill" x1="0" y1="0" x2="0" y2="1"><stop offset="0" stop-color="#3c3c3c"/><stop offset="1" stop-color="#161616"/></linearGradient></defs>
</svg>

<div class="abs service" style="left:229px">
  <svg class="hex" width="120" height="138" viewBox="0 0 120 138"><polygon points="60,0 120,34.5 120,103.5 60,138 0,103.5 0,34.5" fill="url(#hexFill)"/></svg>
  <div class="icon"><svg width="58" height="50" viewBox="0 0 58 50"><rect x="2" y="4" width="14" height="40" rx="2" fill="#f3b21f"/><rect x="20" y="2" width="36" height="28" rx="2" fill="none" stroke="#f3b21f" stroke-width="4"/><rect x="32" y="32" width="12" height="8" fill="#f3b21f"/><rect x="26" y="40" width="24" height="4" fill="#f3b21f"/></svg></div>
  <div class="label">Workstations</div>
</div>
<div class="abs service" style="left:392px">
  <svg class="hex" width="120" height="138" viewBox="0 0 120 138"><polygon points="60,0 120,34.5 120,103.5 60,138 0,103.5 0,34.5" fill="url(#hexFill)"/></svg>
  <div class="icon"><svg width="38" height="54" viewBox="0 0 38 54"><rect x="2" y="0" width="34" height="54" rx="2" fill="#f3b21f"/><rect x="7" y="8" width="24" height="3" fill="#222"/><rect x="7" y="15" width="24" height="3" fill="#222"/><rect x="7" y="22" width="24" height="3" fill="#222"/><rect x="7" y="29" width="24" height="3" fill="#222"/></svg></div>
  <div class="label">Servers</div>
</div>
<div class="abs service" style="left:554px">
  <svg class="hex" width="120" height="138" viewBox="0 0 120 138"><polygon points="60,0 120,34.5 120,103.5 60,138 0,103.5 0,34.5" fill="url(#hexFill)"/></svg>
  <div class="icon"><svg width="54" height="50" viewBox="0 0 54 50"><rect x="14" y="0" width="26" height="12" fill="#f3b21f"/><rect x="0" y="14" width="54" height="22" rx="5" fill="#f3b21f"/><rect x="12" y="30" width="30" height="18" fill="#f3b21f" stroke="#222" stroke-width="3"/><rect x="17" y="37" width="20" height="2" fill="#222"/><rect x="17" y="42" width="20" height="2" fill="#222"/></svg></div>
  <div class="label">Printers</div>
</div>
<div class="abs service" style="left:718px">
  <svg class="hex" width="120" height="138" viewBox="0 0 120 138"><polygon points="60,0 120,34.5 120,103.5 60,138 0,103.5 0,34.5" fill="url(#hexFill)"/></svg>
  <div class="icon" style="top:22px"><svg width="50" height="52" viewBox="0 0 50 52"><rect x="19" y="0" width="12" height="6" fill="#f3b21f"/><circle cx="25" cy="29" r="21" fill="#f3b21f"/><circle cx="25" cy="29" r="12" fill="#222"/><circle cx="25" cy="29" r="6" fill="#f3b21f"/></svg></div>
  <div class="label" style="top:88px">Surveillance<br>Camera</div>
</div>

<h1 class="abs about-title">Tadurk Information Systems <em>PTE LTD (TIS)</em></h1>
<p class="abs about-text">is professionally managed by a core group of visionaries and technologists with decades of industry experience between them and backed by a team of trained professionals at all levels of operations. Perfection is a way of life at TIS. The organization has grown from a small beginning in 1993, to become a company of international repute for reliability. TIS has transformed from a Korvin Reseller to a company providing total IT solutions to companies in Singapore and the Asia region. TIS provides hardware maintenance, networking, software and consulting services.</p>
<div class="abs video" role="img" aria-label="Video still of colourful umbrellas among dark ones">
  <div class="play"><svg width="14" height="18" viewBox="0 0 14 18"><path d="M0 0 L14 9 L0 18 Z" fill="#ffffff"/></svg></div>
</div>

<h2 class="abs col-title" style="left:168px">Contact Us</h2>
<div class="abs map" role="img" aria-label="Street map showing the office location"></div>
<div class="abs address">
  <b>Tadurk Information Systems Pte Ltd</b><br>
  18 Harlow Crescent<br>
  #03-12/14 Elmfield Court<br>
  Singapore - 481205<br>
  <div class="contact-row"><b>Telephone No</b>(065) 6210-4400</div>
  <div class="contact-row"><b>Facsimile No</b>(065) 6210-4407</div>
</div>

<h2 class="abs col-title" style="left:432px">Events &amp; News</h2>
<div class="abs event-date" style="left:433px;top:823px"><span class="d">17</span><span class="m">JAN</span></div>
<p class="abs event-text" style="left:473px;top:821px;width:165px">Lorem ipsum dolor sit amet, consectetuer adipiscing elit, sed diam nonummy nibh euismod tincidunt ut laoreet dolore .</p>
<div class="abs divider-h" style="left:433px;top:884px;width:168px"></div>
<div class="abs event-date" style="left:433px;top:898px"><span class="d">15</span><span class="m">JAN</span></div>
<div class="abs partner-name" style="left:484px;top:900px"><i></i>Veltrix</div>
<p class="abs event-text" style="left:434px;top:942px;width:180px">Lorem ipsum dolor sit amet, consectetuer adipiscing elit, sed diam nonummy nibh euismod tincidunt ut laoreet dolore magna aliquam erat volutpat.</p>

<h2 class="abs col-title" style="left:672px">Testimonials</h2>
<div class="abs quote-mark" style="left:671px;top:812px">&ldquo;</div>
<p class="abs quote-text" style="left:694px;top:816px">We would like to express our appreciation for the prompt and efficient service provided by</p>
<div class="abs quote-mark" style="left:877px;top:832px">&rdquo;</div>
<div class="abs quote-by" style="left:736px;top:852px"><b>Lionel Marsh</b><br>Chief Professor</div>
<div class="abs divider-h" style="left:694px;top:884px;width:170px"></div>
<div class="abs quote-mark" style="left:671px;top:892px">&ldquo;</div>
<p class="abs quote-text" style="left:694px;top:896px">We would like to express our appreciation for the prompt and efficient service provided by</p>
<div class="abs quote-mark" style="left:877px;top:912px">&rdquo;</div>
<div class="abs quote-by" style="left:736px;top:932px"><b>Lionel Marsh</b><br>Chief Professor</div>

<div class="abs partners">
  <div class="label">Media Partners</div>
  <div class="sep" style="left:207px"></div>
  <div class="badge"></div>
  <div class="sep" style="left:376px"></div>
  <div class="p" style="left:390px;color:#0f6b3a">Orvana</div>
  <div class="sep" style="left:474px"></div>
  <div class="p" style="left:496px;color:#1f4d3a">Orvana ERP</div>
  <div class="sep" style="left:617px"></div>
  <div class="p" style="left:636px;color:#1c63b0">Quintel</div>
</div>

<footer class="abs footer"></footer>
<div class="abs footer-links">Home<span>/</span>About Us<span>/</span>Solutions<span>/</span>Services<span>/</span>Event &amp; Promotion<span>/</span>Our Clients</div>
<div class="abs copyright">Copyrights &copy; 2013 Tadurk Information Systems PTE LTD. All rights reserved.</div>
<div class="abs footer-social"><span>Vox</span><span>Qil</span><span>Nod</span><span>Zen</span></div>
<div class="abs footer-brand">
  <div class="brand-dot"></div>
  <div class="brand-name">Tadurk Information<small>Systems PTE LTD</small></div>
</div>

</body>
</html>
```